Stonebrace Business Card Design

The Stonebrace Co is an aggregate (crushing) equipment dealer serving Western Canadian provinces. Stonebrace is a distributor of aggregate equipment for different manufacturers.

We are looking to change and update the existing business card which has been used since the existence of the company. A copy of existing card has been attached for reference. The Stonebrace Co logo we want to remain the same and we want the green color to remain the same.

We are wanting something new with a different look. A refreshing card to show a new modern and updated look. No longer wanting to have the manufacturers on the back of the card but something more like our logo on the back of the card with a statement like "Crushing Solutions"

ideas could be:
- card can be different colors on front and back
- front or reverse of the card could possibly be the green color with the logo in black

Target Market(s)

Owners of Aggregate/Crushing companies

Contact Information for Business Card

see above

Requirements
Must have
• - logo to remain same along with same font within logo
• - green color to remain same
Nice to have
• as noted above under project description
Should not have

```html
<!DOCTYPE html>
<html lang="en">
<head>
<meta charset="utf-8">
<title>Stonebrace Co Business Card</title>
<link href="https://fonts.googleapis.com/css2?family=Roboto+Condensed:ital,wght@0,400;0,700;1,400&display=swap" rel="stylesheet">
<style>
  :root {
    --brand-green: #8a9a0e;
    --ink: #2a2a2a;
    --ink-soft: #555555;
    --paper: #fbfbfb;
    --backdrop: #e9e7e2;
  }
  * { box-sizing: border-box; margin: 0; padding: 0; }
  html, body { width: 1200px; height: 911px; overflow: hidden; }
  body {
    background: var(--backdrop);
    font-family: "Roboto Condensed", sans-serif;
    color: var(--ink);
    position: relative;
  }
  .card {
    position: absolute;
    width: 560px;
    height: 320px;
    border-radius: 22px;
    overflow: hidden;
    box-shadow: 0 10px 26px rgba(0,0,0,0.18);
  }
  .card-front { left: 80px; top: 90px; background: var(--paper); }
  .card-back { left: 560px; top: 500px; background: var(--brand-green); }

  .corner-dot {
    position: absolute;
    right: -28px; top: -28px;
    width: 64px; height: 64px;
    border-radius: 50%;
    background: var(--brand-green);
  }
  .brand-lockup {
    position: absolute;
    display: flex;
    align-items: center;
    gap: 10px;
    font-weight: 700;
    text-transform: uppercase;
    letter-spacing: 0.5px;
  }
  .brand-lockup .brand-dot { border-radius: 50%; flex: none; }
  .card-front .brand-lockup { left: 38px; top: 150px; font-size: 24px; color: var(--ink); }
  .card-front .brand-dot { width: 22px; height: 22px; background: var(--brand-green); }

  .rule {
    position: absolute;
    left: 38px; right: 38px; top: 110px;
    height: 1px;
    background: #4a4a4a;
  }
  .person {
    position: absolute;
    right: 60px; top: 48px;
    text-align: right;
  }
  .person-name {
    font-size: 22px; font-weight: 700; color: var(--brand-green);
    letter-spacing: 0.5px; text-transform: uppercase;
  }
  .person-title {
    font-size: 15px; color: var(--ink); text-transform: uppercase; margin-top: 18px;
  }
  .address {
    position: absolute;
    right: 60px; top: 150px;
    text-align: right;
    font-size: 13px; line-height: 1.4; color: var(--ink-soft);
  }
  .contacts {
    position: absolute;
    left: 38px; bottom: 28px;
    list-style: none;
    font-size: 13px; line-height: 1.45; color: var(--ink-soft);
  }
  .contacts li { display: flex; align-items: center; gap: 8px; }
  .contacts svg { width: 11px; height: 11px; flex: none; }

  .card-back .brand-lockup {
    left: 50%; top: 112px; transform: translateX(-50%);
    font-size: 34px; color: var(--ink); white-space: nowrap;
  }
  .card-back .brand-dot { width: 32px; height: 32px; background: var(--ink); }
  .tagline {
    position: absolute;
    left: 0; right: 0; top: 200px;
    text-align: center;
    font-style: italic; font-size: 16px; color: var(--ink);
  }
</style>
</head>
<body>
  <section class="card card-front" aria-label="Business card front">
    <span class="corner-dot"></span>
    <div class="person">
      <p class="person-name">Dale Morrow</p>
      <p class="person-title">CEO/Founder</p>
    </div>
    <div class="rule"></div>
    <div class="brand-lockup"><span class="brand-dot"></span><span>The Stonebrace Co.</span></div>
    <address class="address">
      2218- 48B Avenue<br>
      Nisku, Alberta T9E 3K1<br>
      www.stonebrace.ca
    </address>
    <ul class="contacts">
      <li>
        <svg viewBox="0 0 12 12"><path d="M2 1 L4.5 1 L5.5 3.5 L4 4.5 Q5 7 7.5 8 L8.5 6.5 L11 7.5 L11 10 Q6 11 2.5 6.5 Q1 4 2 1Z" fill="#8a9a0e"/></svg>
        780.555.0142
      </li>
      <li>
        <svg viewBox="0 0 12 12"><rect x="1" y="2" width="10" height="8" rx="1" fill="none" stroke="#8a9a0e" stroke-width="1.3"/></svg>
        780.555.0187
      </li>
      <li>
        <svg viewBox="0 0 12 12"><rect x="3" y="1" width="6" height="10" rx="1" fill="#8a9a0e"/></svg>
        780.555.0163
      </li>
      <li>
        <svg viewBox="0 0 12 12"><rect x="1" y="2" width="10" height="8" fill="#8a9a0e"/><path d="M1 2 L6 6.5 L11 2" fill="none" stroke="#fff" stroke-width="1"/></svg>
        dale@stonebrace.com
      </li>
    </ul>
  </section>

  <section class="card card-back" aria-label="Business card back">
    <div class="brand-lockup"><span class="brand-dot"></span><span>The Stonebrace Co.</span></div>
    <p class="tagline">Crushing Solutions</p>
  </section>
</body>
</html>
```